Business Cards

I am a landscape designer and I am hired to do over the top landscapes!
I pay attention to detail and do everything from growing my own orchids and Fruits and Vegetables.
I build ponds water features. I do Landscape Lighting and Specialize in Drip Irrigation for New Landscapes.
I am looking for something with a picture of one of my landscapes and pictures of Orchids on the back so I can work on growing my Orchid business.
I like the plastic cards.
I like Saturation
I like color and I want something that really sticks out!
I will attach a few pics!
Thanks
Corey
A Verdant Terrace LLC
Corey Halvorsen
Orchids & Organic Farming
Landscaping Made Simple
561-555-0147
Averdantterrace@mailbrook.net
Harbor Palm Bay FL

Target Market(s)

I work for Wealthy Clients who want unique designs and enjoy rare plants.
I am the goto guy for tropical and rare plants
Cool Designs
Orchids
Interior Decorating
Exterior Lighting
Organic Farming
People who appreciate plants

Industry/Entity Type

Landscape

Font styles to use
Decorative

Requirements
Must have
• COLOR COLOR COLOR
Saturation
Sleek and Clean
Should not have
• tacky

```html
<!DOCTYPE html>
<html lang="en">
<head>
<meta charset="utf-8">
<title>A Verdant Terrace LLC — Business Cards</title>
<link href="https://fonts.googleapis.com/css2?family=Bebas+Neue&family=Montserrat:wght@700&display=swap" rel="stylesheet">
<style>
  :root {
    --page-bg: #eceae6;
    --card-white: #ffffff;
    --ink: #111111;
    --leaf-green: #1fa64a;
    --foliage-dark: #0f5a1e;
    --foliage-mid: #3aa12a;
    --foliage-light: #9bd23a;
    --bloom-red: #d8462a;
    --orchid-violet: #6a1fd6;
    --orchid-magenta: #b42ad0;
    --tag-white: #ffffff;
  }
  * { margin: 0; padding: 0; box-sizing: border-box; }
  html, body { width: 1200px; height: 900px; overflow: hidden; }
  body { background: var(--page-bg); position: relative; }

  .card {
    position: absolute;
    left: 272px;
    width: 652px;
    height: 370px;
    overflow: hidden;
    box-shadow: 0 4px 14px rgba(0,0,0,0.18);
  }
  .card--front { top: 45px; background: var(--card-white); }
  .card--back { top: 482px; }

  .company-name {
    position: absolute;
    left: 26px;
    top: 12px;
    font-family: "Bebas Neue", sans-serif;
    font-weight: 400;
    font-size: 150px;
    line-height: 112px;
    letter-spacing: -1px;
    background: linear-gradient(120deg,
      var(--foliage-dark) 0%, var(--foliage-mid) 22%, var(--bloom-red) 38%,
      var(--foliage-light) 52%, var(--foliage-mid) 70%, var(--foliage-dark) 88%, var(--bloom-red) 100%);
    -webkit-background-clip: text;
    background-clip: text;
    color: transparent;
  }
  .company-name span { display: block; }

  .contact {
    position: absolute;
    right: 28px;
    top: 243px;
    text-align: right;
  }
  .contact__name {
    font-family: "Bebas Neue", sans-serif;
    font-size: 48px;
    line-height: 48px;
    color: var(--ink);
    margin-bottom: 6px;
  }
  .contact__line {
    font-family: "Montserrat", sans-serif;
    font-weight: 700;
    font-size: 16px;
    line-height: 18px;
    color: var(--leaf-green);
  }

  .orchid-photo {
    position: absolute;
    inset: 0;
    background:
      radial-gradient(ellipse at 35% 45%, var(--orchid-violet) 0%, rgba(106,31,214,0.85) 30%, transparent 60%),
      radial-gradient(ellipse at 65% 20%, var(--orchid-magenta) 0%, rgba(106,31,214,0.7) 25%, transparent 55%),
      radial-gradient(ellipse at 85% 75%, var(--orchid-violet) 0%, transparent 45%),
      linear-gradient(135deg, var(--foliage-mid) 0%, var(--foliage-light) 45%, #e89a2a 100%);
  }
  .tagline {
    position: absolute;
    right: 22px;
    bottom: 24px;
    text-align: right;
    font-family: "Bebas Neue", sans-serif;
    font-size: 31px;
    line-height: 29px;
    color: var(--tag-white);
  }
</style>
</head>
<body>
  <section class="card card--front">
    <h1 class="company-name">
      <span>A Verdant</span>
      <span>Terrace</span>
      <span>LLC</span>
    </h1>
    <div class="contact">
      <p class="contact__name">Corey Halvorsen</p>
      <p class="contact__line">561-555-0147</p>
      <p class="contact__line">Averdantterrace@mailbrook.net</p>
      <p class="contact__line">Harbor Palm Bay FL</p>
    </div>
  </section>

  <section class="card card--back">
    <div class="orchid-photo" role="img" aria-label="Close-up photograph of vivid purple orchid blooms against tropical green foliage"></div>
    <p class="tagline">Orchids &amp; Organic Farming<br>Landscaping Made Simple</p>
  </section>
</body>
</html>
```